International service dog training school needs web design

We need to upgrade our website. The website is https://brightmeadow.studio/
We help trainers and service dog programs learn how to train service dogs with the latest and most ethical training methods. We offer online and in-person coaching services. We would like to see designs that are engaging and communicate professionalism, expertise, and care for the dogs and people we work with. Please also keep the colors already in the logo in the design.

```html
<!DOCTYPE html>
<html lang="en">
<head>
<meta charset="utf-8">
<title>Bright Meadow Institute for Assistance Canines</title>
<link href="https://fonts.googleapis.com/css2?family=Montserrat:wght@400;500;600;700;800&display=swap" rel="stylesheet">
<style>
:root{
  --blue:#1a5bb0;
  --blue-dark:#164f9c;
  --teal:#17917f;
  --ink:#111;
  --text:#333;
  --grey-bg:#e9e9e9;
  --pale:#f3f0f0;
  --white:#fff;
}
*{box-sizing:border-box;margin:0;padding:0}
html,body{width:1200px;height:3069px;overflow:hidden}
body{font-family:'Montserrat',sans-serif;color:var(--text);background:var(--white);position:relative}
.abs{position:absolute}
.btn{display:inline-block;background:var(--teal);color:var(--white);font-weight:700;font-size:12px;text-transform:uppercase;padding:10px 16px;text-decoration:none;letter-spacing:.2px}

/* header */
.site-header{height:112px;position:relative;background:var(--white)}
.brand{position:absolute;left:130px;top:24px;display:flex;align-items:center;gap:10px}
.brand-dot{width:58px;height:58px;border-radius:50%;border:3px solid var(--blue)}
.brand-name{font-weight:600;font-size:17px;line-height:1.25;color:var(--blue);width:200px}
.contact-mail{position:absolute;left:820px;top:22px;display:flex;align-items:center;gap:12px}
.mail-badge{width:30px;height:30px;border-radius:50%;background:var(--blue);display:flex;align-items:center;justify-content:center}
.contact-mail small{display:block;font-size:12px;color:var(--ink)}
.contact-mail span{font-size:16px;color:var(--ink)}
.main-nav{position:absolute;right:132px;top:75px;display:flex;gap:37px;font-size:15px;color:var(--ink);font-weight:500}

/* hero */
.hero{height:541px;position:relative;background:linear-gradient(180deg,#5d7a45 0%,#7f9a5a 30%,#b46d62 60%,#b56c5e 90%,#6b8a3f 100%)}
.hero-photo{position:absolute;inset:0;background:radial-gradient(ellipse 220px 260px at 720px 300px,#c99a5a 0%,rgba(201,154,90,0) 100%),linear-gradient(90deg,rgba(0,0,0,.25),rgba(0,0,0,0) 60%)}
.hero h1{position:absolute;left:139px;top:280px;color:var(--white);font-size:44px;font-weight:800;line-height:1.13}
.hero .btn{position:absolute;left:143px;top:403px;font-size:14px;padding:14px 20px}
.slide-arrow{position:absolute;top:246px;width:44px;height:48px;background:var(--white);display:flex;align-items:center;justify-content:center}

/* services */
.services{height:772px;position:relative;background:var(--grey-bg)}
.section-title{text-align:center;font-weight:700;font-size:23px;color:var(--ink)}
.section-title::after{content:"";display:block;width:42px;height:3px;background:var(--teal);margin:17px auto 0}
.services .section-title{padding-top:46px}
.svc-card{position:absolute;background:var(--white);text-align:center}
.svc-card.tall{top:191px;width:292px;height:311px;padding-top:90px}
.icon-circle{width:95px;height:95px;border-radius:50%;background:var(--blue);display:flex;align-items:center;justify-content:center}
.svc-card.tall .icon-circle{position:absolute;left:98px;top:-40px}
.svc-card h3{font-size:16px;font-weight:600;color:var(--ink);line-height:1.5}
.svc-card p{font-size:13px;line-height:1.45;margin:16px auto 28px;width:240px}
.svc-card.wide{top:527px;width:457px;height:188px;text-align:left}
.svc-card.wide .icon-circle{position:absolute;left:43px;top:45px}
.svc-card.wide .body{position:absolute;left:169px;top:36px;width:270px}
.svc-card.wide p{margin:14px 0 18px;width:270px}

/* about */
.about{height:357px;position:relative;background:linear-gradient(90deg,var(--blue-dark),var(--blue))}
.about-mark{position:absolute;left:145px;top:55px;display:flex;align-items:center;gap:14px}
.about-mark .ring{width:120px;height:120px;border-radius:50%;border:8px solid var(--white)}
.about-mark span{color:var(--white);font-weight:600;font-size:16px;width:110px;line-height:1.3}
.about h2{position:absolute;left:450px;top:57px;color:var(--white);font-size:22px;font-weight:700;line-height:1.25}
.about p{position:absolute;left:453px;top:128px;width:615px;color:var(--white);font-size:13px;line-height:1.48}
.about .btn{position:absolute;left:453px;top:274px}

/* courses */
.courses{height:560px;position:relative;background:var(--pale)}
.courses .section-title{padding-top:42px}
.course-card{position:absolute;top:128px;width:299px;height:384px;background:var(--white)}
.course-photo{height:186px}
.course-card h3{font-size:16px;font-weight:600;color:var(--ink);margin:26px 24px 0;line-height:1.3}
.course-card p{font-size:13px;line-height:1.5;margin:12px 25px 0;height:58px}
.course-card .btn{margin:18px 0 0 29px}

/* book */
.book{height:443px;position:relative;background:linear-gradient(90deg,#5b4a33 0%,#9d8a70 35%,#c5b8a2 70%,#a99a80 100%)}
.book-photo{position:absolute;left:0;top:0;width:330px;height:443px;background:linear-gradient(160deg,#6b4a2a,#a06a3a 50%,#3a2a1c)}
.book-panel{position:absolute;left:373px;top:89px;width:470px;height:262px;background:var(--white);padding:40px 0 0 66px}
.book-panel small{font-size:17px;color:var(--ink)}
.book-panel h2{font-size:23px;font-weight:600;color:var(--ink);line-height:1.4;margin-top:12px;width:380px}
.book-panel .btn{margin-top:16px;font-size:13px;padding:13px 19px}
.book-cover{position:absolute;left:843px;top:51px;width:226px;height:342px;background:linear-gradient(180deg,#f4f1ec 0%,#efe8de 45%,#c9a36a 70%,#b3161f 100%)}

/* footer */
.site-footer{height:284px;position:relative;background:var(--blue)}
.footer-brand{position:absolute;left:425px;top:48px;display:flex;align-items:center;gap:14px}
.footer-brand .brand-dot{border-color:var(--white);width:76px;height:76px}
.footer-brand .brand-name{color:var(--white);font-size:21px;width:270px}
.footer-nav{position:absolute;top:163px;left:0;width:1200px;display:flex;justify-content:center;font-size:15px;color:var(--white)}
.footer-nav span{padding:0 18px;border-right:2px solid var(--white);line-height:26px}
.footer-nav span:last-child{border-right:0}
.footer-rule{position:absolute;left:132px;top:222px;width:936px;height:1px;background:rgba(255,255,255,.3)}
.footer-meta{position:absolute;top:243px;left:134px;width:932px;font-size:11px;color:var(--white);display:flex;align-items:center}
.footer-meta .item{display:flex;align-items:center;gap:8px;margin-right:40px}
.footer-meta .copy{margin-left:auto}
</style>
</head>
<body>

<header class="site-header">
  <div class="brand"><div class="brand-dot"></div><div class="brand-name">Miriam Hollis Ph.D. Bright Meadow Institute</div></div>
  <div class="contact-mail">
    <div class="mail-badge"><svg width="14" height="11" viewBox="0 0 14 11"><rect x="0" y="0" width="14" height="11" rx="1.5" fill="#fff"/><path d="M1 1.5 7 6l6-4.5" stroke="#1a5bb0" stroke-width="1.4" fill="none"/></svg></div>
    <div><small>Email us</small><span>info@brightmeadow.studio</span></div>
  </div>
  <nav class="main-nav"><span>The Center</span><span>Helping organizations</span><span>Teaching Trainers</span><span>Research</span><span>Contact</span></nav>
</header>

<section class="hero">
  <div class="hero-photo" role="img" aria-label="Photo of a yellow labrador service dog in a harness sitting on a brick path beside its handler in a park"></div>
  <div class="slide-arrow" style="left:0"><svg width="10" height="14"><path d="M7 2 2 7l5 5" stroke="#222" stroke-width="2" fill="none"/></svg></div>
  <div class="slide-arrow" style="right:0"><svg width="10" height="14"><path d="M3 2l5 5-5 5" stroke="#222" stroke-width="2" fill="none"/></svg></div>
  <h1>Coaching for Service<br>Dog Professionals</h1>
  <a class="btn" href="#">Read more</a>
</section>

<section class="services">
  <h2 class="section-title">OUR SERVICES</h2>

  <div class="svc-card tall" style="left:131px">
    <div class="icon-circle"><svg width="46" height="42" viewBox="0 0 46 42" fill="#fff"><rect x="18" y="2" width="26" height="17" rx="2"/><circle cx="13" cy="20" r="6"/><path d="M2 40c0-9 5-13 11-13s11 4 11 13z"/></svg></div>
    <h3>Organization/<br>Program Consulting</h3>
    <p>Helping organizations get started, improve their training program, and add services</p>
    <a class="btn" href="#">Read more</a>
  </div>
  <div class="svc-card tall" style="left:454px">
    <div class="icon-circle"><svg width="40" height="40" viewBox="0 0 40 40" fill="#fff"><circle cx="20" cy="20" r="16" fill="none" stroke="#fff" stroke-width="4"/><path d="M20 10l3 7h7l-6 4 2 8-6-5-6 5 2-8-6-4h7z"/></svg></div>
    <h3>Professional coaching/<br>teaching for dog trainers</h3>
    <p>Helping dog trainers improve their skills and learn about service dog training and medical alert dog training.</p>
    <a class="btn" href="#">Read more</a>
  </div>
  <div class="svc-card tall" style="left:775px">
    <div class="icon-circle"><svg width="46" height="30" viewBox="0 0 46 30" fill="none" stroke="#fff" stroke-width="4"><rect x="3" y="6" width="22" height="18" rx="9"/><rect x="21" y="6" width="22" height="18" rx="9"/></svg></div>
    <h3>Collaborating in<br>Research Projects</h3>
    <p>Collaborating in research studies in the field of Medical Detection Dogs.</p>
    <a class="btn" href="#">Read more</a>
  </div>

  <div class="svc-card wide" style="left:131px">
    <div class="icon-circle"><svg width="44" height="40" viewBox="0 0 44 40" fill="#fff"><rect x="14" y="4" width="28" height="20" rx="1"/><circle cx="8" cy="14" r="4"/><rect x="4" y="20" width="8" height="18"/></svg></div>
    <div class="body"><h3>Presentations and Seminars</h3><p>Sharing knowledge about service dogs and medical detection.</p><a class="btn" href="#">Read more</a></div>
  </div>
  <div class="svc-card wide" style="left:610px">
    <div class="icon-circle"><svg width="48" height="48" viewBox="0 0 48 48" fill="none" stroke="#fff" stroke-width="3.5"><circle cx="24" cy="24" r="20"/><ellipse cx="24" cy="24" rx="9" ry="20"/><path d="M4 24h40"/></svg></div>
    <div class="body"><h3>International services</h3><p>Fluent in both English and French, in-person and online coaching around the</p><a class="btn" href="#">Read more</a></div>
  </div>
</section>

<section class="about">
  <div class="about-mark"><div class="ring"></div><span>Bright Meadow Institute</span></div>
  <h2>THE BRIGHT MEADOW INSTITUTE<br>FOR ASSISTANCE CANINES</h2>
  <p>The Bright Meadow Institute for Assistance Canines was founded by Miriam Hollis Ph.D. in response to demand for coaching from dog trainers, medical professionals, and service dog programs. Miriam Hollis Ph.D. has helped hundreds of trainers and several programs both in the US and internationally, expand the type of dogs they could offer to include medical alert dogs. Specialized mostly in the training of diabetic alert dogs, seizure dogs, and psychiatric service dogs, Miriam Hollis is also experienced in the training of mobility assistance dogs and autism dogs.</p>
  <a class="btn" href="#">Read more</a>
</section>

<section class="courses">
  <h2 class="section-title">COURSES</h2>
  <article class="course-card" style="left:131px">
    <div class="course-photo" role="img" aria-label="Photo of dogs resting in kennel runs" style="background:linear-gradient(135deg,#a89e88,#c9c0aa 50%,#6f6654)"></div>
    <h3>Dog Selection</h3>
    <p>What dogs have the most potential to be service dogs. How to test for temperament</p>
    <a class="btn" href="#">Read more</a>
  </article>
  <article class="course-card" style="left:451px">
    <div class="course-photo" role="img" aria-label="Photo of trainers seated in a classroom during a seminar" style="background:linear-gradient(135deg,#8a8a7a,#c2b6a0 50%,#5a5046)"></div>
    <h3>Service Dog Training<br>and Assessments</h3>
    <p>This course will give you a complete system to train service dogs along...</p>
    <a class="btn" href="#">Read more</a>
  </article>
  <article class="course-card" style="left:770px">
    <div class="course-photo" role="img" aria-label="Photo of a trainer working with a dog on scent discrimination indoors" style="background:linear-gradient(135deg,#b9b5ac,#dcd7cc 50%,#7d5a3a)"></div>
    <h3>Scent discrimination, alerting behaviors and more</h3>
    <p>Become a professional medical assistant dog trainer! In this course,</p>
    <a class="btn" href="#">Read more</a>
  </article>
</section>

<section class="book">
  <div class="book-photo" role="img" aria-label="Photo of a German shepherd in a harness lying on the ground"></div>
  <div class="book-panel">
    <small>New book from Miriam Hollis Ph.D.!</small>
    <h2>Choosing And Preparing Your Service Dog: Steps to Thrive in Public Access Work</h2>
    <a class="btn" href="#">Click here</a>
  </div>
  <div class="book-cover" role="img" aria-label="Book cover showing a labrador in a red service vest"></div>
</section>

<footer class="site-footer">
  <div class="footer-brand"><div class="brand-dot"></div><div class="brand-name">Miriam Hollis Ph.D. Bright Meadow Institute</div></div>
  <nav class="footer-nav"><span>The Center</span><span>Helping organizations</span><span>Teaching Trainers</span><span>Research</span><span>Contact</span></nav>
  <div class="footer-rule"></div>
  <div class="footer-meta">
    <div class="item"><svg width="9" height="12" viewBox="0 0 9 12"><path d="M4.5 0A4.5 4.5 0 0 0 0 4.5C0 8 4.5 12 4.5 12S9 8 9 4.5A4.5 4.5 0 0 0 4.5 0z" fill="#fff"/><circle cx="4.5" cy="4.5" r="1.6" fill="#1a5bb0"/></svg>2480 Linden Park Rd Springfield IL 62704</div>
    <div class="item"><svg width="12" height="9" viewBox="0 0 12 9"><rect width="12" height="9" rx="1" fill="#fff"/><path d="M1 1l5 4 5-4" stroke="#1a5bb0" fill="none"/></svg>info@brightmeadow.studio</div>
    <div class="copy">Copyright © 2021 All Rights Reserved</div>
  </div>
</footer>

</body>
</html>
```